Brookvane Consulting Business Card Design

Business Card Design for Brookvane Consulting. Brookvane Consulting is a boutique consultancy based in Atlanta, GA., that specializes in marketing strategy, organization planning, and leadership development. We provide solutions for small businesses and startups as well as Vantage 300 companies.

http://brookvaneconsulting.com/

Target Market(s)

We provide solutions for small businesses and startups as well as Vantage 300 companies.

Industry/Entity Type

Consulting

Contact Information for Business Card

Two sided business card with priority on contact information, logo, tag line (Guidance to Plan Well, Lead Well, Grow Well)

Colors

Designer to choose colors to be used in the design.

Requirements
Must have
• contact information, logo, tag line (Guidance to Plan Well, Lead Well, Grow Well)
• Simple no over communication.
Nice to have
• I would like to see different placements of logo and creative use of both sides of the card
Should not have
• Do not put too much information on the card.

```html
<!DOCTYPE html>
<html lang="en">
<head>
<meta charset="utf-8">
<title>Brookvane Consulting Business Card</title>
<link rel="stylesheet" href="https://fonts.googleapis.com/css2?family=Montserrat:wght@400;600&family=Kaushan+Script&display=swap">
<style>
  :root {
    --backdrop: #3b3b3b;
    --card-dark: #2f2f30;
    --card-light: #f3f3f2;
    --ink-dark: #1e1e1e;
    --ink-silver: #c9c9c9;
    --ink-muted: #444444;
  }
  * { margin: 0; padding: 0; box-sizing: border-box; }
  html, body {
    width: 799px;
    height: 1200px;
    overflow: hidden;
    background: var(--backdrop);
    font-family: "Montserrat", sans-serif;
  }
  .sheet {
    position: relative;
    width: 799px;
    height: 1200px;
  }
  .card {
    position: absolute;
    left: 60px;
    width: 680px;
    height: 389px;
    border-radius: 30px;
    box-shadow: 0 18px 40px rgba(0, 0, 0, 0.45);
  }
  .card--front {
    top: 140px;
    background: var(--card-dark);
  }
  .card--back {
    top: 670px;
    background: var(--card-light);
  }
  .logo {
    position: absolute;
    display: flex;
    align-items: center;
    gap: 14px;
    white-space: nowrap;
  }
  .logo__mark {
    width: 22px;
    height: 22px;
    flex: none;
  }
  .logo__name {
    font-weight: 600;
    letter-spacing: 0.5px;
  }
  .card--front .logo {
    left: 0;
    right: 0;
    top: 168px;
    justify-content: center;
  }
  .card--front .logo__mark { background: var(--ink-silver); }
  .card--front .logo__name {
    font-size: 42px;
    color: var(--ink-silver);
  }
  .holder-name {
    position: absolute;
    left: 58px;
    top: 52px;
    font-family: "Kaushan Script", cursive;
    font-size: 24px;
    color: var(--ink-dark);
  }
  .brand-block {
    position: absolute;
    right: 48px;
    top: 150px;
    width: 320px;
  }
  .card--back .logo { position: static; }
  .card--back .logo__mark { background: var(--ink-dark); width: 16px; height: 16px; }
  .card--back .logo__name {
    font-size: 24px;
    color: var(--ink-dark);
  }
  .tagline {
    margin-top: 8px;
    font-size: 10.5px;
    color: var(--ink-muted);
    letter-spacing: 0.2px;
    white-space: nowrap;
  }
  .contact {
    position: absolute;
    left: 58px;
    bottom: 62px;
    list-style: none;
    font-size: 15px;
    line-height: 22px;
    color: var(--ink-dark);
  }
</style>
</head>
<body>
<main class="sheet">
  <section class="card card--front" aria-label="Card front">
    <div class="logo">
      <span class="logo__mark"></span>
      <span class="logo__name">Brookvane Consulting</span>
    </div>
  </section>

  <section class="card card--back" aria-label="Card back">
    <p class="holder-name">Dorian</p>
    <div class="brand-block">
      <div class="logo">
        <span class="logo__mark"></span>
        <span class="logo__name">Brookvane Consulting</span>
      </div>
      <p class="tagline">Guidance to Plan Well, Lead Well, Grow Well</p>
    </div>
    <ul class="contact">
      <li>404-555-0172</li>
      <li>dorian@brookvaneconsulting.com</li>
      <li>www.brookvaneconsulting.com</li>
    </ul>
  </section>
</main>
</body>
</html>
```